Belvascotravel.com web design project + logo design

Hi,

We are a Russian online tour operator - sunkettle.com

We are looking to tranmsfer our domain to belvascotravel.com. The website and logo need to be belvascoesque - we are not looking to change our functionality, but we need to make the website much more attracitve to clients, much more wild looking but at the same time remaining a professional travel company.

The main concept of the website should be innovative travel (as belvasco was an innovator). Alternatively, you could go down the artist route and go down the draw / design your own tour road.

On our website the customer is able to combine travel services (hotels, flights, Visa services, and soon chauffeur, car rental etc...) put it into their basket (the basket definitely has to look better than it is at the moment) and pay for it in one go by card.

We are also stressin our customer support with web chat, call centre etc... (call centre number at the top of the page)

We aim to provide an easy user experience, but we need to make it have some more style, so I will be waiting for what you guys can come up with.
Let me know if you have any questions - skype is: mrdolbarin

Industry/Entity Type

It Company

Requirements
Must have
• It is quite a simple task - to take the existing website sunkettle.com and belvascosize it to create belvascotravel.com, the functionality of the website will remain the same and there are not many pages in the website. Homepage, Checkout step1, Checkout step 2 (you can view both of these if you select a service) and the generic pages for T&C''s, Privacy policy etc...

IMPORTANT UPDATE

We are also looking at how the search results will look in the designs, (please do a search on our website for hotel / flight)

```html
<!DOCTYPE html>
<html lang="en">
<head>
<meta charset="utf-8">
<title>Belvasco Travel</title>
<link href="https://fonts.googleapis.com/css2?family=Roboto:wght@300;400;500&display=swap" rel="stylesheet">
<style>
:root{
  --blue:#17b4ee;
  --pink:#f0479b;
  --dark:#3d3d3d;
  --grey-band:#ebebeb;
  --text:#555;
  --label-pink:#e8408f;
  --night-1:#1a1030;
  --night-2:#5a2d5e;
  --night-3:#2c2a4a;
}
*{box-sizing:border-box;margin:0;padding:0}
html,body{width:756px;height:1200px;overflow:hidden;background:#fff}
body{font-family:"Roboto",Arial,sans-serif;color:var(--text);position:relative}
.abs{position:absolute}

/* hero */
.hero-photo{left:0;top:0;width:756px;height:366px;
  background:linear-gradient(180deg,#241a2c 0%,var(--night-3) 20%,var(--night-2) 55%,#7a4a5a 80%,#3a3048 100%)}
.top-bar{left:0;top:0;width:756px;height:64px;background:rgba(20,12,20,.55)}
.brand{left:126px;top:12px;display:flex;align-items:center;gap:6px}
.brand-dot{width:28px;height:28px;border-radius:50%;background:#fff}
.brand-name{color:#fff;font-weight:400;font-size:22px;line-height:1}
.lang{left:592px;top:12px;width:39px;height:10px;background:#eee;font-size:6px;color:#333;padding-left:3px;line-height:10px}
.lang::after{content:"";position:absolute;right:1px;top:1px;width:8px;height:8px;background:#555}
.call-box{left:498px;top:26px;width:133px;height:30px;background:var(--blue);color:#fff;display:flex;align-items:center;padding-left:8px;gap:6px}
.call-number{font-size:14px;font-weight:300;line-height:1}
.call-hours{font-size:6px;line-height:1.2}
.side-btn{left:582px;width:48px;height:16px;background:#fff;font-size:6px;color:var(--pink);display:flex;align-items:center;gap:4px;padding-left:4px}
.side-btn i{width:7px;height:7px;border-radius:50%;background:#444;display:block}

/* tabs + form */
.tab{top:163px;height:19px;width:55px;font-size:7px;color:#ccc;background:#555;text-align:center;line-height:19px}
.tab.active{background:var(--blue);color:#fff}
.ticket-form{left:126px;top:182px;width:372px;height:126px;background:#fff}
.ticket-form .lbl{position:absolute;font-size:7.5px;color:var(--label-pink)}
.field{position:absolute;height:16px;border:2px solid #e4e4e4;font-size:6px;color:#aaa;padding-left:4px;line-height:12px;background:#fff}
.field.filled{color:#444}
.sel-arrow{position:absolute;right:2px;top:2px;width:8px;height:8px;background:#444}
.tiny{position:absolute;font-size:5px;color:#aaa}
.chk{position:absolute;font-size:5.5px;color:#666;display:flex;align-items:center;gap:3px}
.chk b{width:6px;height:6px;background:#ddd;display:block}
.btn-dark{position:absolute;background:var(--dark);color:#fff;font-size:11px;text-align:center;font-weight:300;border-bottom:2px solid #222}

/* basket */
.basket{left:502px;top:182px;width:128px;height:126px;background:#fff}
.basket-head{height:19px;background:var(--blue);color:#222;font-size:11px;text-align:center;line-height:19px}
.basket-cart{position:absolute;left:42px;top:24px}
.basket-pay{position:absolute;top:72px;width:128px;height:16px;background:var(--pink);color:#fff;font-size:7.5px;text-align:center;line-height:16px}
.basket-cards{position:absolute;top:88px;width:128px;height:20px;background:#d8d8d8;display:flex;justify-content:center;align-items:center;gap:3px}
.basket-cards span{width:16px;height:10px;background:#fff;border:1px solid #999;display:block}
.basket-pricing{position:absolute;top:108px;width:128px;height:18px;background:#555;color:#fff;font-size:7.5px;text-align:center;line-height:18px}

.hotel-tab{left:126px;top:336px;width:118px;height:30px;background:#fff;padding:3px 4px}
.hotel-tab p{font-size:9px;color:#222}
.book-now{display:inline-block;background:var(--pink);color:#fff;font-size:7px;padding:0 4px;line-height:10px}

/* search strip */
.search-strip{left:0;top:366px;width:756px;height:94px;background:linear-gradient(#fff,#f1f1f1)}
.strip-line{left:0;top:458px;width:756px;height:2px;background:var(--blue)}
.step{top:384px;height:12px;background:var(--blue);color:#222;font-size:6px;line-height:12px;padding-left:4px}
.opt{left:126px;font-size:5.5px;color:#444;display:flex;align-items:center;gap:5px}
.opt b{width:7px;height:6px;border:1px solid #bbb;display:block}
.small-lbl{top:402px;font-size:6px;color:#333}
.spin{top:411px;height:15px;width:38px;border:1px solid #ccc;background:#fff;font-size:6px;color:#333;padding-left:4px;line-height:13px}

/* sections */
.band-grey{left:0;width:756px;background:var(--grey-band)}
.sec-tag{left:126px;background:#555;color:#fff;font-weight:300;font-size:14px;padding:0 6px;line-height:24px;height:24px}
.headline{left:0;width:756px;text-align:center;color:var(--pink);font-weight:300;font-size:24px}
.visa-opt{font-size:12.5px;color:#333;text-align:center;width:240px}
.btn-blue{background:var(--blue);color:#fff;font-size:7.5px;text-align:center;line-height:19px;height:19px;width:55px;border-bottom:2px solid #0d8ec0}
.tickets-art{left:126px;top:680px;width:505px;height:204px;background:linear-gradient(180deg,#fff 0%,#eee9f2 55%,#e6e3e8 100%)}
.tickets-title{left:225px;top:755px;width:306px;height:38px;background:#fff;border:1px solid #ddd;color:var(--pink);font-weight:300;font-size:23px;text-align:center;line-height:36px}
.tickets-text{left:126px;top:806px;width:505px;height:44px;background:#fff;border:1px solid #ddd;font-size:6.6px;line-height:1.6;padding:5px 10px;color:#666}
.hotels-text{left:126px;top:998px;width:496px;font-size:6.8px;line-height:1.65;color:#666}

/* footer */
.offers{left:474px;top:1072px;width:157px;height:48px;background:#fff;padding:5px 8px}
.offers h4{font-size:8.5px;font-weight:500;color:#222}
.email-row{margin-top:6px;height:14px;display:flex}
.email-in{flex:1;background:var(--pink);color:#fff;font-size:5.5px;line-height:14px;padding-left:6px;border-radius:7px 0 0 7px}
.email-send{width:42px;background:#222;color:#fff;font-size:6.5px;text-align:center;line-height:14px;border-radius:7px}
.footer{left:0;top:1096px;width:756px;height:83px;background:var(--blue)}
.foot-col{top:1110px;color:#fff}
.foot-col h5{font-size:8px;font-weight:400;color:#222;margin-bottom:9px}
.foot-col p{font-size:5.6px;line-height:10px;display:flex;align-items:center;gap:4px}
.foot-col p i{width:7px;height:7px;border-radius:50%;background:#fff;display:block}
.foot-brand{left:528px;top:1132px;display:flex;align-items:center;gap:6px}
.bottom-bar{left:0;top:1179px;width:756px;height:21px;background:var(--dark);color:#ddd;font-size:5.6px;text-align:center;line-height:21px}
</style>
</head>
<body>

<div class="abs hero-photo" role="img" aria-label="Night city skyline with lit skyscrapers and a passenger plane"></div>
<div class="abs top-bar"></div>
<div class="abs brand"><span class="brand-dot"></span><span class="brand-name">Belvasco Travel</span></div>
<div class="abs lang">English</div>
<div class="abs call-box">
  <svg width="14" height="14" viewBox="0 0 24 24"><path fill="#fff" d="M6.6 10.8a15 15 0 0 0 6.6 6.6l2.2-2.2c.3-.3.7-.4 1-.2 1.1.4 2.3.6 3.6.6.6 0 1 .4 1 1V20c0 .6-.4 1-1 1A17 17 0 0 1 3 4c0-.6.4-1 1-1h3.5c.6 0 1 .4 1 1 0 1.3.2 2.5.6 3.6.1.3 0 .7-.2 1z"/></svg>
  <div><div class="call-number">8-800-555-0142</div><div class="call-hours">(Mon-Fri) Hours: 9:00 am - 18:00</div></div>
</div>
<div class="abs side-btn" style="top:69px"><i></i>My Tour</div>
<div class="abs side-btn" style="top:93px"><i></i>Web Chat</div>

<div class="abs tab active" style="left:126px">TICKETS</div>
<div class="abs tab" style="left:184px">INFO</div>
<div class="abs tab" style="left:240px">HOTELS</div>

<form class="abs ticket-form">
  <span class="lbl" style="left:10px;top:21px">Whence</span>
  <div class="field" style="left:60px;top:12px;width:104px">Type...</div>
  <span class="lbl" style="left:183px;top:17px">Where</span>
  <div class="field" style="left:226px;top:12px;width:104px">Type...</div>

  <span class="lbl" style="left:10px;top:43px">There</span>
  <div class="field filled" style="left:60px;top:35px;width:104px">30-5-2013</div>
  <span class="lbl" style="left:183px;top:43px">Back</span>
  <div class="field filled" style="left:226px;top:35px;width:60px">16-6-2013</div>
  <span class="chk" style="left:292px;top:35px"><b style="background:#bbb"></b>Back</span>
  <span class="chk" style="left:292px;top:44px"><b></b>One way</span>

  <span class="tiny" style="left:66px;top:56px">Men</span>
  <span class="tiny" style="left:102px;top:56px">Women</span>
  <span class="tiny" style="left:142px;top:56px">Children</span>
  <span class="lbl" style="left:10px;top:70px">Passengers</span>
  <div class="field filled" style="left:60px;top:64px;width:22px">1<span class="sel-arrow"></span></div>
  <div class="field filled" style="left:100px;top:64px;width:23px">1<span class="sel-arrow"></span></div>
  <div class="field filled" style="left:140px;top:64px;width:23px">1<span class="sel-arrow"></span></div>
  <span class="lbl" style="left:183px;top:68px">Class</span>
  <div class="field filled" style="left:226px;top:64px;width:104px">Economy<span class="sel-arrow"></span></div>

  <div class="btn-dark" style="left:149px;top:96px;width:73px;height:23px;line-height:21px">Search</div>
</form>

<div class="abs basket">
  <div class="basket-head">BASKET</div>
  <svg class="basket-cart" width="46" height="44" viewBox="0 0 46 44">
    <circle cx="2" cy="4" r="2" fill="#17b4ee"/>
    <path d="M3 5 L10 8 L14 28 H40" stroke="#666" stroke-width="2" fill="none"/>
    <path d="M11 10 H44 L40 25 H14 Z" fill="#fff" stroke="#999" stroke-width="1.5"/>
    <path d="M16 13 L38 22 M22 11 L36 24 M30 11 L20 24" stroke="#f0479b" stroke-width="1" opacity=".7"/>
    <circle cx="17" cy="36" r="3.5" fill="#fff" stroke="#222" stroke-width="2"/>
    <circle cx="36" cy="36" r="3.5" fill="#fff" stroke="#222" stroke-width="2"/>
  </svg>
  <div class="basket-pay">Payment</div>
  <div class="basket-cards"><span></span><span></span><span></span><span></span><span></span></div>
  <div class="basket-pricing">*Pricing</div>
</div>

<div class="abs hotel-tab"><p>Search for A Hotel / Flight</p><span class="book-now">Book Now</span></div>

<div class="abs search-strip"></div>
<div class="abs strip-line"></div>
<div class="abs step" style="left:126px;width:40px">01. What?</div>
<div class="abs step" style="left:213px;width:40px">02. Where?</div>
<div class="abs step" style="left:397px;width:36px">03. When?</div>
<div class="abs step" style="left:506px;width:39px">04. Who?</div>
<div class="abs opt" style="top:402px"><b></b>Hotels</div>
<div class="abs opt" style="top:416px"><b></b>Flights</div>
<div class="abs opt" style="top:430px"><b></b>Cars</div>
<div class="abs field" style="left:213px;top:403px;width:131px;height:15px;border-width:1px;border-color:#ccc">Lorem Ipsum Dolor<span class="sel-arrow"></span></div>
<div class="abs field" style="left:397px;top:402px;width:57px;height:15px;border-width:1px;border-color:#ccc">Check In</div>
<div class="abs field" style="left:397px;top:422px;width:57px;height:15px;border-width:1px;border-color:#ccc">Check Out</div>
<div class="abs small-lbl" style="left:506px">Rooms</div>
<div class="abs small-lbl" style="left:550px">Adults</div>
<div class="abs small-lbl" style="left:593px">Child</div>
<div class="abs spin" style="left:506px">01</div>
<div class="abs spin" style="left:550px">01</div>
<div class="abs spin" style="left:593px">01</div>
<div class="btn-dark" style="left:570px;top:445px;width:62px;height:19px;line-height:17px;font-size:8px;font-weight:400">Search</div>

<section>
  <div class="abs band-grey" style="top:480px;height:198px"></div>
  <div class="abs sec-tag" style="top:492px">INFO</div>
  <h2 class="abs headline" style="top:522px">There are two option apply for visa</h2>
  <p class="abs visa-opt" style="left:157px;top:572px">1. Oformlenie visa “Online”</p>
  <p class="abs visa-opt" style="left:388px;top:572px">2. Visa “Myself.”</p>
  <svg class="abs" style="left:267px;top:604px" width="20" height="30" viewBox="0 0 20 30"><path d="M7 0h6v18h7L10 30 0 18h7z" fill="#111"/></svg>
  <svg class="abs" style="left:498px;top:604px" width="20" height="30" viewBox="0 0 20 30"><path d="M7 0h6v18h7L10 30 0 18h7z" fill="#111"/></svg>
  <div class="abs btn-blue" style="left:250px;top:643px">Click Here</div>
  <div class="abs btn-blue" style="left:480px;top:643px">Click Here</div>
</section>

<section>
  <div class="abs tickets-art" role="img" aria-label="Faint sketch of world landmarks and an airliner"></div>
  <div class="abs sec-tag" style="top:690px">TICKETS</div>
  <h2 class="abs tickets-title">Flights from Tours designer.</h2>
  <p class="abs tickets-text">On our site you can consider offers from different airlines and purchase tickets according to your wishes and budget. Plan dates of departures and arrivals c in any country, filling the cells you want, Tour Designer automatically displays your program in the calendar. On Tour Designer You can create any tour, including round-the-world and pay for all the services a single payment.</p>
</section>

<section>
  <div class="abs band-grey" style="top:898px;height:164px"></div>
  <div class="abs sec-tag" style="top:908px">HOTELS</div>
  <h2 class="abs headline" style="top:946px">Hotels by City Builder.</h2>
  <p class="abs hotels-text">Our site offers a wide selection of hotels located in different countries and continents of the world. You can choose and book all kinds of accommodation options, according to your wishes and budget. pursue their dreams! We have created for you the most convenient framework for planning a vacation or business trip. Tour Builder saves your time now to buy a package tour you can just 3 simple steps: Choose the services Confirm requested services, payment of a single payment. A complete set of documents confirming the purchase tour package will be on our website in your personal account, send documents to "Print".</p>
</section>

<footer>
  <div class="abs footer"></div>
  <div class="abs offers">
    <h4>Exclusive Offers</h4>
    <div class="email-row"><span class="email-in">Email Address</span><span class="email-send">Send</span></div>
  </div>
  <div class="abs foot-col" style="left:126px"><h5>View Site</h5><p>Home</p><p>About Us</p><p>Form</p><p>Contacts</p></div>
  <div class="abs foot-col" style="left:190px"><h5>Follow Us</h5><p><i></i>Friendbook</p><p><i></i>Chirper</p><p><i></i>Blog</p></div>
  <div class="abs foot-col" style="left:264px"><h5>Contact Us</h5><p>+7 (495) 555-01-37</p><p>8-800-555-0142</p><p>info@belvascotravel.com</p></div>
  <div class="abs foot-col" style="left:366px"><h5>Find Us</h5><p>Tour Builder Limited 14</p><p>Harlow Street London,</p><p>W2 4QX UK</p></div>
  <div class="abs foot-brand"><span class="brand-dot"></span><span class="brand-name">Belvasco Travel</span></div>
  <div class="abs bottom-bar">© 2012–2013 BelvascoTravel, Terms &amp; Conditions : Privacy Policy</div>
</footer>

</body>
</html>
```